i need a business card for a plumbing company in california

we are a drain cleaning , maintenance plumbing company who is starting new marketing campaign for a tatrench-less pipe installation department .

Target Market(s)

the professional who appreciates time and quality workmanship.

Industry/Entity Type

Plumbing

Colors
0655a3
ec1f27

Requirements
Must have
• the second logo needs to be included
Nice to have
• a focus on the services offered
Should not have
• any underlined words on the brief

```html
<!DOCTYPE html>
<html lang="en">
<head>
<meta charset="utf-8">
<title>Clearline Plumbing – Business Card</title>
<link rel="stylesheet" href="https://fonts.googleapis.com/css2?family=Arimo:wght@400;700&display=swap">
<style>
  :root {
    --backdrop: #d8d1c7;
    --card-light: #f1efed;
    --card-shade: #dedad6;
    --brand-red: #c4161d;
    --brand-red-deep: #9e0f14;
    --swoosh: #3a3a38;
    --ink: #4a4a4a;
    --ink-soft: #5a5a5a;
    --on-red: #f2f2f2;
  }
  * { margin: 0; padding: 0; box-sizing: border-box; }
  html, body { width: 1200px; height: 970px; overflow: hidden; }
  body {
    background: var(--backdrop);
    font-family: "Arimo", Arial, sans-serif;
    position: relative;
  }
  .business-card {
    position: absolute;
    left: 80px;
    top: 190px;
    width: 1040px;
    height: 590px;
    border-radius: 30px;
    overflow: hidden;
    background: linear-gradient(160deg, var(--card-light) 0%, #f7f6f5 45%, var(--card-shade) 100%);
    box-shadow: 0 18px 40px rgba(0,0,0,0.18);
  }
  .card-art { position: absolute; inset: 0; width: 1040px; height: 590px; }
  .holder {
    position: absolute;
    right: 46px;
    top: 58px;
    text-align: right;
    color: var(--on-red);
  }
  .holder-name { font-weight: 700; font-size: 30px; letter-spacing: 0.5px; line-height: 1.1; }
  .holder-role { font-size: 25px; line-height: 1.2; }
  .wordmark {
    position: absolute;
    left: 46px;
    top: 272px;
    display: flex;
    align-items: center;
    gap: 18px;
  }
  .wordmark-name {
    font-weight: 700;
    font-size: 58px;
    line-height: 1.0;
    color: var(--ink);
  }
  .wordmark-dot {
    width: 26px; height: 26px;
    border-radius: 50%;
    background: var(--brand-red);
  }
  .rule {
    position: absolute;
    left: 46px;
    right: 54px;
    top: 463px;
    height: 3px;
    background: var(--brand-red);
  }
  .contacts {
    position: absolute;
    left: 46px;
    top: 482px;
    display: flex;
    gap: 36px;
    color: var(--ink-soft);
    font-size: 25px;
  }
  .contact-col { display: flex; flex-direction: column; gap: 8px; }
  .contact-item { display: flex; align-items: center; gap: 12px; height: 30px; white-space: nowrap; }
  .contact-icon { width: 30px; height: 30px; flex: none; }
  .address { padding-top: 0; line-height: 38px; margin-left: 8px; }
</style>
</head>
<body>
  <section class="business-card" aria-label="Clearline Plumbing business card">
    <svg class="card-art" viewBox="0 0 1040 590" aria-hidden="true">
      <defs>
        <linearGradient id="redBand" x1="0" y1="0" x2="1" y2="1">
          <stop offset="0" stop-color="#d0232a"/>
          <stop offset="0.55" stop-color="#c4161d"/>
          <stop offset="1" stop-color="#a51117"/>
        </linearGradient>
      </defs>
      <path class="red-band" d="M0,0 H1040 V372 C820,70 330,10 0,80 Z" fill="url(#redBand)"/>
      <path class="swoosh" d="M28,88 C330,38 820,92 1040,390 V445 C830,130 360,62 28,88 Z" fill="var(--swoosh)"/>
    </svg>

    <div class="holder">
      <p class="holder-name">DANA MORLEY</p>
      <p class="holder-role">Manager</p>
    </div>

    <div class="wordmark">
      <p class="wordmark-name">Clearline<br>Plumbing</p>
      <span class="wordmark-dot"></span>
    </div>

    <div class="rule"></div>

    <div class="contacts">
      <div class="contact-col">
        <p class="contact-item">
          <svg class="contact-icon" viewBox="0 0 30 30" aria-hidden="true"><circle cx="15" cy="15" r="13" fill="none" stroke="#c4161d" stroke-width="2"/><path d="M9 13c0-3 3-4 6-4s6 1 6 4l-2 1-1-2h-6l-1 2zM10 15h10v6H10z" fill="#c4161d"/></svg>
          (01) 4821 3370
        </p>
        <p class="contact-item">
          <svg class="contact-icon" viewBox="0 0 30 30" aria-hidden="true"><circle cx="15" cy="15" r="13" fill="none" stroke="#c4161d" stroke-width="2"/><path d="M11 8h8v5h-8zM8 13h14v7H8zM11 18h8v4h-8z" fill="#c4161d"/></svg>
          (01) 4821 3370
        </p>
      </div>
      <div class="contact-col">
        <p class="contact-item">
          <svg class="contact-icon" viewBox="0 0 30 30" aria-hidden="true"><circle cx="15" cy="15" r="13" fill="none" stroke="#c4161d" stroke-width="2"/><rect x="8" y="10" width="14" height="10" fill="#c4161d"/><path d="M8 10l7 6 7-6" fill="none" stroke="#fff" stroke-width="1.4"/></svg>
          hello@clearlinepro.com
        </p>
        <p class="contact-item">
          <svg class="contact-icon" viewBox="0 0 30 30" aria-hidden="true"><circle cx="15" cy="15" r="13" fill="none" stroke="#c4161d" stroke-width="2"/><circle cx="15" cy="15" r="7.5" fill="none" stroke="#c4161d" stroke-width="1.6"/><ellipse cx="15" cy="15" rx="3.2" ry="7.5" fill="none" stroke="#c4161d" stroke-width="1.4"/><path d="M7.5 15h15" stroke="#c4161d" stroke-width="1.4"/></svg>
          www.clearlinepro.com
        </p>
      </div>
      <div class="address">
        <p>PO BOX 418 Harbor Avenue</p>
        <p>Oakland, CA, USA</p>
      </div>
    </div>
  </section>
</body>
</html>
```